Clear Path Keystone Realty yard sign Logo

UPDATE Design logo for Realty yard sign. 24x24 diamond or 36x24 Rectangle.
Open to all ideas. We are a discount firm but want to project a high end feel. We provide 100% of all services and extensive marketing for 1/2 the fee.
The following info must be on sign
CLEAR PATH KEYSTONE (OR K) REALTY
Doran Pike 547-6093
KeystonePX.com

Target Market(s)

home sellers and buyers

Industry/Entity Type

Real Estate yard sign please see sign attached in gif

Logo Text

Clear Path Keystone Realty OR (K IN PLACE OF KEYSTONE)

Requirements
Must have
• CLEAR PATH KEYSTONE (OR K) REALTY Doran Pike 547-6093 KeystonePX.com FOR SALE (optional)

```html
<!DOCTYPE html>
<html lang="en">
<head>
<meta charset="utf-8">
<title>Clear Path Keystone Realty – Yard Sign</title>
<link rel="stylesheet" href="https://fonts.googleapis.com/css2?family=Arimo:wght@700&display=swap">
<style>
  :root {
    --page-bg: #ffffff;
    --frame-black: #0a0a0a;
    --brand-gold: #c99a2e;
    --agent-gold: #c8962a;
    --silver: #cfcfcf;
    --silver-ring: #b9b9b9;
    --shadow-dark: rgba(0, 0, 0, 0.45);
  }
  html, body {
    margin: 0;
    padding: 0;
    overflow: hidden;
    background: var(--page-bg);
  }
  .yard-sign {
    position: relative;
    width: 1200px;
    height: 1000px;
    background: var(--page-bg);
    font-family: "Arimo", Arial, sans-serif;
  }
  .sign-frame {
    position: absolute;
    inset: 0;
  }
  .brand-name,
  .agent-line,
  .web-address {
    position: absolute;
    left: 0;
    width: 1200px;
    margin: 0;
    text-align: center;
    font-weight: 700;
  }
  .brand-name {
    top: 428px;
    font-size: 52px;
    line-height: 62px;
    letter-spacing: 2px;
    color: var(--brand-gold);
  }
  .agent-line {
    top: 582px;
    font-size: 50px;
    line-height: 56px;
    color: var(--agent-gold);
    text-shadow: 2px 3px 3px var(--shadow-dark);
  }
  .web-address {
    top: 650px;
    font-size: 34px;
    line-height: 40px;
    color: var(--silver);
    text-shadow: 1px 2px 2px var(--shadow-dark);
  }
</style>
</head>
<body>
  <main class="yard-sign">
    <svg class="sign-frame" width="1200" height="1000" viewBox="0 0 1200 1000" aria-hidden="true">
      <polygon points="600,106 994,500 600,894 206,500"
               fill="none" stroke="var(--frame-black)" stroke-width="13" stroke-linejoin="miter"/>
      <circle class="brand-mark-circle" cx="600" cy="325" r="78"
              fill="none" stroke="var(--silver-ring)" stroke-width="18"/>
    </svg>

    <h1 class="brand-name">CLEAR PATH<br>KEYSTONE REALTY</h1>
    <p class="agent-line">Doran Pike 547-6093</p>
    <p class="web-address">KeystonePX.com</p>
  </main>
</body>
</html>
```